App UI design needed! For a Password Management Tool

Need a design of a Windows desktop application which is a Password Management Tool, similar to 9tidewell, Quillmark or Brimsoft, with Business/Enterprise functionalities. Here attached are a few sample pages of Quillmark, and some sample pages of our app called Veltrika. We certainly want to redesign our app.
We need: 1. The layout of the web: top banner, menu, main pane; 2. Form style, main form and sub forms; 3. List style; 4 Fonts and buttons; 5. Logo.
The design should look professional, can attract business customers as well as individual users, and present a strong sense of “Security”. The look and feel should differentiate from well-known products like 9tidewell, Quillmark, Brimsoft, etc.

```html
<!DOCTYPE html>
<html lang="en">
<head>
<meta charset="utf-8">
<title>Veltrika – Password Manager UI</title>
<link href="https://fonts.googleapis.com/css2?family=Poppins:wght@400;500;600;700&display=swap" rel="stylesheet">
<style>
:root{
  --board:#646a51;
  --blue:#0a7bd0;
  --blue-text:#0a7bd0;
  --dark:#2a2d34;
  --gray-bg:#f1f1f1;
  --row-hi:#e5e5e5;
  --line:#dcdcdc;
  --text:#333;
  --muted:#555;
  --yellow:#f7c51e;
  --green:#3aaa35;
  --brand:#3ea3f2;
  --purple:#6a3fc9;
}
*{box-sizing:border-box;margin:0;padding:0}
html,body{width:1200px;height:707px;overflow:hidden;background:var(--board)}
body{font-family:'Poppins',sans-serif;color:var(--text)}
.board{position:absolute;left:0;top:0;width:2518px;height:1484px;transform:scale(0.47657);transform-origin:0 0}
.screen{position:absolute;width:1171px;height:658px;background:var(--gray-bg);overflow:hidden}
.s1{left:56px;top:60px}.s2{left:1277px;top:60px}.s3{left:56px;top:773px}.s4{left:1277px;top:773px}
.topbar{position:absolute;left:0;top:0;width:100%;height:67px;background:#fff}
.top-icons{position:absolute;top:19px;left:1044px;display:flex;gap:6px;align-items:center}
.top-icons span{width:25px;height:26px;display:flex;align-items:center;justify-content:center}
.top-icons .on{background:var(--blue);border-radius:50%;color:#fff}
.top-icons svg{width:13px;height:13px;fill:#777}
.top-icons .on svg{fill:#fff}
.sidebar{position:absolute;left:26px;top:0;width:202px;height:658px;background:var(--blue);border-radius:52px;overflow:hidden}
.brand{height:67px;background:var(--dark);display:flex;align-items:center;justify-content:center;gap:6px;padding-top:6px}
.brand-mark{width:20px;height:20px;border:3px solid var(--brand);border-radius:50%}
.brand-name{color:var(--brand);font-size:19px;font-weight:500}
.nav-item{position:absolute;left:0;width:202px;height:45px;border-bottom:1px dashed rgba(255,255,255,.35);display:flex;align-items:center;color:#fff;font-size:12px;font-weight:600}
.nav-item svg{position:absolute;left:12px;width:13px;height:13px;fill:var(--yellow)}
.nav-item b{position:absolute;left:38px;font-weight:600}
.nav-item.sub b{left:64px}
.nav-item.sub i{position:absolute;left:38px;font-style:normal}
.nav-item.active{left:8px;width:194px;background:#fff;color:var(--blue-text);border-radius:23px 0 0 23px;border-bottom:none}
.nav-item.active svg{left:21px;fill:var(--dark)}
.nav-item.active b{left:56px}
.page-title{position:absolute;left:268px;top:84px;font-size:20px;font-weight:600;color:#333}
.rule{position:absolute;left:268px;top:126px;width:877px;height:1px;background:#d8d8d8}
.search{position:absolute;top:145px;height:32px;background:#fff;border:1px solid #c9c9c9;font-size:12px;color:#555;padding:0 9px;display:flex;align-items:center;justify-content:space-between}
.search svg{width:12px;height:12px;fill:#333}
.btn-new{position:absolute;top:145px;height:32px;border:1px solid var(--blue);background:#fff;color:var(--blue);font-size:12px;display:flex;align-items:center;justify-content:center}
.table{position:absolute;left:268px;width:877px;background:#fff}
.thead{height:46px;background:var(--dark);color:#fff;font-size:14px;font-weight:600;position:relative}
.row{position:relative;border-bottom:1px solid #e7e7e7;font-size:14px;color:#333}
.row.hi{background:var(--row-hi)}
.cell{position:absolute;top:50%;transform:translateY(-50%);white-space:nowrap}
.circ{position:absolute;top:50%;transform:translateY(-50%);width:32px;height:32px;border:2px solid var(--blue);border-radius:50%;display:flex;align-items:center;justify-content:center}
.circ svg{width:15px;height:15px;fill:var(--blue)}
.pager{position:absolute;right:27px;font-size:11px;color:#333}
.x10{position:absolute;left:1138px;top:633px;font-size:11px;color:var(--purple)}
.modal{position:absolute;left:679px;top:86px;width:492px;height:572px;background:#fff}
.modal-head{height:40px;background:var(--blue);color:#fff;font-size:14px;font-weight:500;display:flex;align-items:center;justify-content:space-between;padding:0 14px}
.m{position:absolute;font-size:12px;color:#333}
.input{position:absolute;height:35px;border:1px solid #d3d3d3;font-size:12px;display:flex;align-items:center;padding-left:10px;color:#333}
.radio{display:inline-block;width:10px;height:10px;border:1px solid #aaa;border-radius:50%;vertical-align:-1px;margin-right:4px}
.mtable{position:absolute;left:17px;top:359px;width:379px;height:92px;border:1px solid #c9c9c9;font-size:11px}
.mtable .h{height:32px;background:#efefef;font-weight:600;position:relative;border-bottom:1px solid #c9c9c9}
.mtable .r{height:28px;position:relative}
.mtable .r.sel{background:#e6f1fb}
.mtable span{position:absolute;top:50%;transform:translateY(-50%)}
.mbtn{position:absolute;top:463px;height:32px;border:1px solid #bbb;font-size:12px;display:flex;align-items:center;justify-content:center;background:#fff}
.list-panel{position:absolute;left:268px;top:126px;width:378px;height:532px;background:#fff}
.list-item{position:absolute;left:10px;width:360px;height:36px}
.list-item .circ{left:10px}
.list-item .t{position:absolute;left:48px;top:50%;transform:translateY(-50%);font-size:12px;color:#333;white-space:nowrap}
.card{position:absolute;left:665px;width:478px;background:#fff;border:1px solid #e4e4e4}
.lbl{position:absolute;left:14px;font-size:11px;color:#444}
.val{position:absolute;left:14px;font-size:14px;font-weight:600;color:#222}
.status{color:var(--green)}
.act{position:absolute;top:50%;transform:translateY(-50%);width:14px;height:14px;fill:var(--blue)}
</style>
</head>
<body>
<svg width="0" height="0" style="position:absolute" aria-hidden="true">
  <symbol id="i-dash" viewBox="0 0 16 16"><path d="M8 2a7 7 0 0 0-7 7v3h14V9a7 7 0 0 0-7-7zm0 8a1.5 1.5 0 0 1-1-2.6L11 5l-2.4 4.3A1.5 1.5 0 0 1 8 10z"/></symbol>
  <symbol id="i-user" viewBox="0 0 16 16"><circle cx="8" cy="5" r="3.5"/><path d="M1 15c0-4 3-6 7-6s7 2 7 6z"/></symbol>
  <symbol id="i-team" viewBox="0 0 16 16"><circle cx="8" cy="5" r="2.5"/><circle cx="3" cy="6" r="2"/><circle cx="13" cy="6" r="2"/><path d="M3 14c0-3 2-5 5-5s5 2 5 5zM0 13c0-2 1-4 3-4l1 1-1 3zM16 13c0-2-1-4-3-4l-1 1 1 3z"/></symbol>
  <symbol id="i-flag" viewBox="0 0 16 16"><path d="M1 3l4-1 6 2 4-1v10l-4 1-6-2-4 1z"/></symbol>
  <symbol id="i-laptop" viewBox="0 0 16 16"><path d="M3 3h10v7H3zm1.5 1.5v4h7v-4zM0 12h16v1.5H0z"/></symbol>
  <symbol id="i-pie" viewBox="0 0 16 16"><path d="M7 2a6.5 6.5 0 1 0 7 7H7z"/><path d="M9 0v7h7A7 7 0 0 0 9 0z"/></symbol>
  <symbol id="i-star" viewBox="0 0 16 16"><path d="M8 1l2.2 4.6 5 .6-3.7 3.4 1 5L8 12.2 3.5 14.6l1-5L.8 6.2l5-.6z"/></symbol>
  <symbol id="i-key" viewBox="0 0 16 16"><circle cx="10.5" cy="5.5" r="4.5"/><path d="M6.5 8L1 13.5V15h3v-2h2v-2l2-2z"/></symbol>
  <symbol id="i-tag" viewBox="0 0 16 16"><path d="M1 1h7l7 7-7 7-7-7zm3.5 2a1.5 1.5 0 1 0 0 3 1.5 1.5 0 0 0 0-3z"/></symbol>
  <symbol id="i-dollar" viewBox="0 0 16 16"><path d="M7 1h2v2c2 .3 3 1.4 3 3H10c0-.8-.7-1.2-2-1.2S6 5.2 6 6s.8 1 2.5 1.4C11 8 12 9 12 10.6c0 1.5-1.1 2.6-3 2.9V15H7v-1.5c-2-.3-3.2-1.5-3.2-3.2H6c0 .9.8 1.5 2.1 1.5s2-.5 2-1.2-.7-1-2.4-1.5C5.4 9.6 4.2 8.7 4.2 7 4.2 5.5 5.3 4.4 7 4.1z"/></symbol>
  <symbol id="i-home" viewBox="0 0 16 16"><path d="M8 1l8 7h-2v7h-4v-5H6v5H2V8H0z"/></symbol>
  <symbol id="i-bars" viewBox="0 0 16 16"><path d="M1 3h14v2H1zm0 4h14v2H1zm0 4h14v2H1z"/></symbol>
  <symbol id="i-bell" viewBox="0 0 16 16"><path d="M8 1a5 5 0 0 0-5 5v4l-2 2v1h14v-1l-2-2V6a5 5 0 0 0-5-5zm-2 13a2 2 0 0 0 4 0z"/></symbol>
  <symbol id="i-dots" viewBox="0 0 16 16"><circle cx="8" cy="3" r="1.6"/><circle cx="8" cy="8" r="1.6"/><circle cx="8" cy="13" r="1.6"/></symbol>
  <symbol id="i-search" viewBox="0 0 16 16"><path d="M6.5 1a5.5 5.5 0 0 1 4.4 8.8l4.1 4.1-1.4 1.4-4.1-4.1A5.5 5.5 0 1 1 6.5 1zm0 2a3.5 3.5 0 1 0 0 7 3.5 3.5 0 0 0 0-7z"/></symbol>
  <symbol id="i-info" viewBox="0 0 16 16"><circle cx="8" cy="3" r="1.7"/><path d="M6 6h3.5v7H11v2H5v-2h1.5V8H6z"/></symbol>
  <symbol id="i-pencil" viewBox="0 0 16 16"><path d="M11 1l4 4-9 9H2v-4zM1 15h4l-4-4z"/></symbol>
  <symbol id="i-trash" viewBox="0 0 16 16"><path d="M5 0h6v2h4v2H1V2h4zM2 5h12l-1 11H3z"/></symbol>
</svg>

<div class="board">

  <!-- Screen 1: web logins with edit form -->
  <section class="screen s1">
    <div class="topbar">
      <div class="top-icons">
        <span><svg><use href="#i-home"/></svg></span>
        <span class="on"><svg><use href="#i-bars"/></svg></span>
        <span><svg><use href="#i-bell"/></svg></span>
        <span><svg><use href="#i-dots"/></svg></span>
      </div>
    </div>
    <nav class="sidebar">
      <div class="brand"><div class="brand-mark"></div><div class="brand-name">Veltrika</div></div>
      <div class="nav-item" style="top:71px"><svg><use href="#i-dash"/></svg><b>Dashboard</b></div>
      <div class="nav-item" style="top:116px"><svg><use href="#i-user"/></svg><b>Users</b></div>
      <div class="nav-item" style="top:161px"><svg><use href="#i-team"/></svg><b>Team</b></div>
      <div class="nav-item" style="top:206px"><svg><use href="#i-flag"/></svg><b>Client Containers</b></div>
      <div class="nav-item active" style="top:250px"><svg><use href="#i-laptop"/></svg><b>Web Logins</b></div>
      <div class="nav-item" style="top:296px;border-bottom:none"><svg><use href="#i-pie"/></svg><b>Reports</b></div>
    </nav>
    <h1 class="page-title">Web Logins</h1>
    <div class="rule"></div>
    <div class="search" style="left:268px;width:379px">Search<svg><use href="#i-search"/></svg></div>
    <div class="btn-new" style="left:657px;width:77px">+ New</div>
    <div class="table" style="top:188px">
      <div class="thead"><span class="cell" style="left:18px">Name</span><span class="cell" style="left:229px">Username</span></div>
      <div class="row" style="height:48px"><span class="cell" style="left:18px">exchange.orvanta</span><span class="cell" style="left:229px">my orvanta \ h_wei</span></div>
      <div class="row" style="height:48px"><span class="cell" style="left:18px">Socialnest</span><span class="cell" style="left:229px">mlin@mailbox.test</span></div>
      <div class="row hi" style="height:50px"><span class="cell" style="left:18px">Codeforge</span><span class="cell" style="left:229px">mlin@mailbox.test</span></div>
      <div class="row" style="height:50px"><span class="cell" style="left:18px">Talentia - default</span><span class="cell" style="left:229px">l_wei@orvanta.com</span></div>
    </div>
    <div class="modal">
      <div class="modal-head"><span>Web Login</span><span>X</span></div>
      <div class="m" style="left:17px;top:57px">Web Login Name*</div>
      <div class="input" style="left:17px;top:83px;width:448px">Codeforge</div>
      <div class="m" style="left:17px;top:128px">Login Page URL*</div>
      <div class="input" style="left:17px;top:154px;width:448px">https://codeforge.io/login</div>
      <div class="m" style="left:17px;top:198px">User Name*</div>
      <div class="m" style="left:254px;top:198px">Password*</div>
      <div class="input" style="left:17px;top:223px;width:209px">mlin@mailbox.test</div>
      <div class="input" style="left:254px;top:223px;width:210px">*************</div>
      <div class="m" style="left:32px;top:278px;color:var(--blue);font-weight:500">Assign</div>
      <div class="m" style="left:170px;top:278px;font-weight:500">Bind A Client Container</div>
      <div style="position:absolute;left:17px;top:302px;width:447px;height:1px;background:#ddd"></div>
      <div style="position:absolute;left:17px;top:300px;width:72px;height:3px;background:var(--blue)"></div>
      <div class="m" style="left:17px;top:326px"><span class="radio"></span>Not Specified</div>
      <div class="m" style="left:129px;top:326px"><span class="radio"></span>Client Container</div>
      <div class="mtable">
        <div class="h"><span style="left:9px">Machine Description</span><span style="left:220px">IP</span></div>
        <div class="r sel"><span style="left:9px">Desktop China 10...</span><span style="left:220px">10.... 10.24.118.42</span></div>
        <div class="r"><span style="left:9px">Desktop China 10...</span><span style="left:220px">10.... 10.24.118.42</span></div>
      </div>
      <div class="mbtn" style="left:17px;width:76px">Cancel</div>
      <div class="mbtn" style="left:102px;width:76px;border-color:var(--blue);color:var(--blue)">Save</div>
      <div class="m" style="left:16px;top:508px">Created 2022-03-24 17:31:29 (GMT+08:00)</div>
      <div class="m" style="left:16px;top:530px">Modified 2022-03-24 17:31:41 (GMT+08:00)</div>
    </div>
  </section>

  <!-- Screen 2: web login detail -->
  <section class="screen s2">
    <div class="topbar">
      <div class="top-icons">
        <span class="on"><svg><use href="#i-home"/></svg></span>
        <span><svg><use href="#i-bars"/></svg></span>
        <span><svg><use href="#i-bell"/></svg></span>
        <span><svg><use href="#i-dots"/></svg></span>
      </div>
    </div>
    <nav class="sidebar">
      <div class="brand"><div class="brand-mark"></div><div class="brand-name">Veltrika</div></div>
      <div class="nav-item" style="top:76px;height:34px"><svg><use href="#i-star"/></svg><b>Favourites</b></div>
      <div class="nav-item" style="top:110px;height:34px"><svg><use href="#i-star"/></svg><b>ORVT</b></div>
      <div class="nav-item" style="top:144px;height:36px"><svg><use href="#i-key"/></svg><b>Web Logins</b></div>
      <div class="nav-item" style="top:191px;height:26px;border:none"><svg><use href="#i-tag"/></svg><b>Tags</b></div>
      <div class="nav-item sub" style="top:218px;height:28px;border:none"><i>#</i><b>Orvanta tag</b></div>
      <div class="nav-item sub" style="top:246px;height:28px;border:none"><i>#</i><b>News</b></div>
      <div class="nav-item sub" style="top:273px;height:28px;border:none"><i>#</i><b>Office</b></div>
      <div class="nav-item sub" style="top:301px;height:30px"><i>#</i><b>Source code</b></div>
      <div class="nav-item" style="top:332px;height:34px"><svg><use href="#i-user"/></svg><b>Personal</b></div>
      <div class="nav-item" style="top:366px;height:34px"><svg><use href="#i-laptop"/></svg><b>Web Logins</b></div>
      <div class="nav-item" style="top:403px;height:26px;border:none"><svg><use href="#i-tag"/></svg><b>My Tags</b></div>
      <div class="nav-item sub" style="top:430px;height:28px"><i>#</i><b>你好</b></div>
      <div class="nav-item" style="top:462px;height:34px;border:none"><svg><use href="#i-dollar"/></svg><b>Payment</b></div>
    </nav>
    <h1 class="page-title">Web Logins</h1>
    <div class="rule"></div>
    <div class="list-panel">
      <div class="search" style="left:10px;top:19px;width:353px">Search<svg><use href="#i-search"/></svg></div>
      <div class="list-item" style="top:68px"><div class="circ"><svg><use href="#i-key"/></svg></div><span class="t">exchange.orvanta my orvanta \ h_wei</span></div>
      <div class="list-item" style="top:119px"><div class="circ"></div><span class="t">Socialnest mlin@mailbox.test</span></div>
      <div class="list-item" style="top:169px"><div class="circ"></div><span class="t">Codeforge mlin@mailbox.test</span></div>
      <div class="list-item" style="top:218px"><div class="circ"><svg><use href="#i-info"/></svg></div><span class="t">Talentia-default l_wei@orvanta.com</span></div>
    </div>
    <div class="m" style="left:1090px;top:143px;color:#444;font-size:12px"><svg style="width:10px;height:10px;fill:#444"><use href="#i-pencil"/></svg> Edit</div>
    <svg style="position:absolute;left:1136px;top:145px;width:12px;height:12px;fill:#333"><use href="#i-dots"/></svg>
    <div style="position:absolute;left:665px;top:189px;width:48px;height:48px;border:2px solid var(--blue);border-radius:50%"></div>
    <div style="position:absolute;left:728px;top:193px;font-size:28px;font-weight:500;color:#333">Codeforge</div>
    <div class="card" style="top:258px;height:94px">
      <div class="lbl" style="top:13px">Login User Name</div>
      <div class="val" style="top:30px">mlin@mailbox.test</div>
      <div style="position:absolute;left:0;top:60px;width:100%;height:1px;background:#e4e4e4"></div>
      <div class="lbl" style="top:67px;color:var(--blue)">Login Password: ************</div>
    </div>
    <div class="card" style="top:366px;height:61px">
      <div class="lbl" style="top:10px">Login Page URL</div>
      <div class="val" style="top:27px">https://codeforge.io/login</div>
    </div>
    <div class="card" style="top:439px;height:61px">
      <div class="lbl" style="top:10px">Client Container</div>
      <div class="val" style="top:27px">Desktop-China-10.24.118.42</div>
    </div>
    <div class="x10">x10</div>
  </section>

  <!-- Screen 3: client containers -->
  <section class="screen s3">
    <div class="topbar">
      <div class="top-icons">
        <span><svg><use href="#i-home"/></svg></span>
        <span class="on"><svg><use href="#i-bars"/></svg></span>
        <span><svg><use href="#i-bell"/></svg></span>
        <span><svg><use href="#i-dots"/></svg></span>
      </div>
    </div>
    <nav class="sidebar">
      <div class="brand"><div class="brand-mark"></div><div class="brand-name">Veltrika</div></div>
      <div class="nav-item" style="top:71px"><svg><use href="#i-dash"/></svg><b>Dashboard</b></div>
      <div class="nav-item" style="top:116px"><svg><use href="#i-user"/></svg><b>Users</b></div>
      <div class="nav-item" style="top:161px"><svg><use href="#i-team"/></svg><b>Team</b></div>
      <div class="nav-item active" style="top:207px"><svg><use href="#i-flag"/></svg><b>Client Containers</b></div>
      <div class="nav-item" style="top:252px"><svg><use href="#i-laptop"/></svg><b>Web Logins</b></div>
      <div class="nav-item" style="top:298px;border-bottom:none"><svg><use href="#i-pie"/></svg><b>Reports</b></div>
    </nav>
    <h1 class="page-title">Client Containers</h1>
    <div class="rule"></div>
    <div class="search" style="left:268px;width:379px">Search<svg><use href="#i-search"/></svg></div>
    <div class="btn-new" style="left:657px;width:77px">+ New</div>
    <div class="table" style="top:189px">
      <div class="thead" style="height:45px"><span class="cell" style="left:18px">Client Containers Des...</span><span class="cell" style="left:229px">IP</span><span class="cell" style="left:440px">Remarks</span><span class="cell" style="left:677px">Status</span></div>
      <div class="row" style="height:50px"><span class="cell" style="left:18px">Desktop China 10...</span><span class="cell" style="left:229px">10.... 10.24.118.42</span><span class="cell" style="left:440px">Clients-1</span><span class="cell status" style="left:677px">Active</span></div>
      <div class="row" style="height:53px;border:none"><span class="cell" style="left:18px">Desktop China 10...</span><span class="cell" style="left:229px">10.... 10.24.118.42</span><span class="cell" style="left:440px">Clients-2</span><span class="cell status" style="left:677px">Active</span></div>
    </div>
    <div class="pager" style="top:359px">1-2- of Items &nbsp;‹ [ 1 ] › &nbsp;20/page</div>
    <div class="x10">x10</div>
  </section>

  <!-- Screen 4: web logins list -->
  <section class="screen s4">
    <div class="topbar">
      <div class="top-icons">
        <span><svg><use href="#i-home"/></svg></span>
        <span class="on"><svg><use href="#i-bars"/></svg></span>
        <span><svg><use href="#i-bell"/></svg></span>
        <span><svg><use href="#i-dots"/></svg></span>
      </div>
    </div>
    <nav class="sidebar">
      <div class="brand"><div class="brand-mark"></div><div class="brand-name">Veltrika</div></div>
      <div class="nav-item" style="top:71px"><svg><use href="#i-dash"/></svg><b>Dashboard</b></div>
      <div class="nav-item" style="top:116px"><svg><use href="#i-user"/></svg><b>Users</b></div>
      <div class="nav-item" style="top:161px"><svg><use href="#i-team"/></svg><b>Team</b></div>
      <div class="nav-item" style="top:206px"><svg><use href="#i-flag"/></svg><b>Client Containers</b></div>
      <div class="nav-item active" style="top:251px"><svg><use href="#i-laptop"/></svg><b>Web Logins</b></div>
      <div class="nav-item" style="top:296px;border-bottom:none"><svg><use href="#i-pie"/></svg><b>Reports</b></div>
    </nav>
    <h1 class="page-title">Web Logins</h1>
    <div class="rule"></div>
    <div class="search" style="left:268px;width:379px">Search<svg><use href="#i-search"/></svg></div>
    <div class="btn-new" style="left:657px;width:77px">+ New</div>
    <div class="table" style="top:189px">
      <div class="thead" style="height:46px"><span class="cell" style="left:18px">Name</span><span class="cell" style="left:282px">Username</span><span class="cell" style="left:545px">Login Page URL</span></div>
      <div class="row" style="height:48px"><div class="circ" style="left:17px"><svg><use href="#i-key"/></svg></div><span class="cell" style="left:71px">exchange.orvanta</span><span class="cell" style="left:282px">my orvanta \ h_wei</span><span class="cell" style="left:545px">https://exchangeorvanta.com</span></div>
      <div class="row" style="height:48px"><div class="circ" style="left:17px"></div><span class="cell" style="left:71px">Socialnest</span><span class="cell" style="left:282px">mlin@mailbox.test</span><span class="cell" style="left:545px">https://www.socialnest.com</span></div>
      <div class="row hi" style="height:48px"><div class="circ" style="left:17px"></div><span class="cell" style="left:71px">Codeforge</span><span class="cell" style="left:282px">mlin@mailbox.test</span><span class="cell" style="left:545px">https://codeforge.io/login</span>
        <svg class="act" style="left:755px"><use href="#i-key"/></svg><svg class="act" style="left:796px"><use href="#i-pencil"/></svg><svg class="act" style="left:836px"><use href="#i-trash"/></svg></div>
      <div class="row" style="height:51px;border:none"><div class="circ" style="left:17px"><svg><use href="#i-info"/></svg></div><span class="cell" style="left:71px">Talentia - default</span><span class="cell" style="left:282px">l_wei@orvanta.com</span><span class="cell" style="left:545px">https://www.talentia.cn/Login</span></div>
    </div>
    <div class="pager" style="top:455px">1-4- of 4 Items &nbsp;‹ [ 1 ] › &nbsp;20/page</div>
    <div class="x10">x10</div>
  </section>

</div>
</body>
</html>
```